Automotive Business Card Design

I would just like a automotive themed card. nothing too extravagant, but catchy.

needs to say something about doing roadside assistance,mobile repairs, Diesel repairs, and Fleet maintenance

it can be single sided or double sided. no preference there.

Industry/Entity Type

Automotive

Contact Information for Business Card

Dean Marlowe
phone 534 861 2093
Name: Brightpath Automotive & Diesel Repair

```html
<!DOCTYPE html>
<html lang="en">
<head>
<meta charset="utf-8">
<title>Brightpath Automotive &amp; Diesel Repair – Business Card</title>
<link href="https://fonts.googleapis.com/css2?family=Open+Sans:wght@400;600;700&display=swap" rel="stylesheet">
<style>
  :root {
    --page-bg: #e4e5e6;
    --card-bg: #ffffff;
    --card-shade: #f1f2f3;
    --ink: #1c1c1c;
    --ink-soft: #333333;
    --ink-muted: #5a5f63;
    --accent: #3ab6e3;
    --accent-deep: #1f8fcf;
  }
  * { box-sizing: border-box; margin: 0; padding: 0; }
  html, body {
    width: 1200px;
    height: 1005px;
    overflow: hidden;
    background: var(--page-bg);
    font-family: "Open Sans", Arial, sans-serif;
  }
  .canvas { position: relative; width: 1200px; height: 1005px; }
  .card {
    position: absolute;
    left: 210px;
    width: 780px;
    height: 446px;
    background: linear-gradient(135deg, var(--card-bg) 0%, var(--card-bg) 60%, var(--card-shade) 100%);
    box-shadow: 0 6px 18px rgba(0, 0, 0, 0.18);
  }
  .card--back { top: 45px; }
  .card--front { top: 514px; }

  .brand {
    display: flex;
    align-items: center;
    gap: 14px;
    color: var(--ink);
    font-weight: 600;
    font-size: 26px;
    letter-spacing: 0.5px;
    white-space: nowrap;
  }
  .brand__dot {
    width: 22px; height: 22px;
    border-radius: 50%;
    background: var(--accent);
    flex: none;
  }
  .back-block {
    position: absolute;
    left: 0; right: 0; top: 50%;
    transform: translateY(-50%);
    display: flex;
    flex-direction: column;
    align-items: center;
    gap: 18px;
  }
  .services {
    display: flex;
    gap: 12px;
    list-style: none;
    font-size: 16px;
    color: var(--ink-muted);
    letter-spacing: 0.4px;
  }
  .services li + li::before {
    content: "•";
    color: var(--accent);
    margin-right: 12px;
  }
  .card--front .brand {
    position: absolute;
    left: 190px;
    top: 120px;
  }

  .accent-bar {
    position: absolute;
    left: 40px; top: 0;
    width: 9px; height: 100%;
    background: linear-gradient(180deg, var(--accent) 0%, var(--accent-deep) 100%);
  }

  .contact {
    position: absolute;
    left: 88px;
    top: 250px;
    color: var(--ink-soft);
  }
  .contact__title {
    font-size: 25px;
    font-weight: 700;
    color: var(--ink);
  }
  .contact__name {
    font-size: 18px;
    font-weight: 600;
    color: var(--accent-deep);
    margin: 2px 0 8px;
  }
  .contact__list { list-style: none; }
  .contact__item {
    display: flex;
    align-items: center;
    gap: 10px;
    font-size: 20px;
    line-height: 31px;
  }
  .contact__icon { width: 14px; height: 14px; flex: none; fill: var(--ink-soft); }
</style>
</head>
<body>
<main class="canvas">

  <section class="card card--back" aria-label="Business card back">
    <div class="back-block">
      <div class="brand">
        <span class="brand__dot"></span>
        <span class="brand__name">Brightpath Automotive &amp; Diesel Repair</span>
      </div>
      <ul class="services">
        <li>Roadside Assistance</li>
        <li>Mobile Repairs</li>
        <li>Diesel Repairs</li>
        <li>Fleet Maintenance</li>
      </ul>
    </div>
  </section>

  <section class="card card--front" aria-label="Business card front">
    <div class="accent-bar"></div>
    <div class="brand">
      <span class="brand__dot"></span>
      <span class="brand__name">Brightpath Automotive &amp; Diesel Repair</span>
    </div>
    <div class="contact">
      <h2 class="contact__title">Contact Me</h2>
      <p class="contact__name">Dean Marlowe</p>
      <ul class="contact__list">
        <li class="contact__item">
          <svg class="contact__icon" viewBox="0 0 16 16" aria-hidden="true"><path d="M4 1l3 3-2 2c1 2 3 4 5 5l2-2 3 3-2 3C7 15 1 9 1 3z"/></svg>
          <span>534 861 2093</span>
        </li>
        <li class="contact__item">
          <svg class="contact__icon" viewBox="0 0 16 16" aria-hidden="true"><path d="M1 3h14v10H1z M2 4l6 5 6-5" stroke="#fff" stroke-width="1.2"/></svg>
          <span>dean@brightpathauto.com</span>
        </li>
        <li class="contact__item">
          <svg class="contact__icon" viewBox="0 0 16 16" aria-hidden="true"><circle cx="8" cy="8" r="7"/><path d="M1 8h14M8 1c-3 3-3 11 0 14M8 1c3 3 3 11 0 14" stroke="#fff" stroke-width="1" fill="none"/></svg>
          <span>www.brightpathauto.com</span>
        </li>
      </ul>
    </div>
  </section>

</main>
</body>
</html>
```